TalkHarbor - Language Coaching Services

Sleek, innovative, trendy design for Language Coaching business.

TalkHarbor is a new UK based company that provides Language Coaching services. We offer highly personalized on-line and face to face language courses. We also impart learning techniques workshops based on the latest neuroscience research for second-language acquisition.

Target Market(s)

See attached info

Industry/Entity Type

Consulting

Contact Information for Business Card

TalkHarbor
DaniaKV@talkharbor.co.uk
TalkHarbor.co.uk
London, UK

Font styles to use
Sans Serif

```html
<!DOCTYPE html>
<html lang="en">
<head>
<meta charset="utf-8">
<title>TalkHarbor – Business Card</title>
<link rel="stylesheet" href="https://fonts.googleapis.com/css2?family=Open+Sans:ital,wght@0,400;0,600;1,700&display=swap">
<style>
  :root {
    --brand-blue: #1a8fc4;
    --brand-blue-dark: #0d79ad;
    --ink: #2b2b2b;
    --rule-dark: #1f1f1f;
    --card-white: #ffffff;
    --stage: #e9ecef;
  }
  * { box-sizing: border-box; margin: 0; padding: 0; }
  html, body { width: 1200px; height: 900px; overflow: hidden; }
  body {
    background: var(--stage);
    font-family: "Open Sans", Arial, sans-serif;
    color: var(--ink);
    position: relative;
  }
  .card {
    position: absolute;
    background: var(--card-white);
    border-radius: 22px;
    overflow: hidden;
    box-shadow: 0 10px 28px rgba(0,0,0,0.18);
  }

  /* Front face */
  .card--front { left: 440px; top: 60px; width: 660px; height: 377px; z-index: 2; }
  .front__ring {
    position: absolute; left: -120px; top: 28px;
    width: 330px; height: 330px;
    border: 14px solid var(--brand-blue);
    border-radius: 50%;
  }
  .front__identity { position: absolute; left: 300px; top: 92px; }
  .front__name {
    font-weight: 600; font-size: 40px; letter-spacing: 1px;
    color: var(--brand-blue); text-transform: uppercase; line-height: 1;
  }
  .front__url { margin-top: 6px; font-size: 17px; font-weight: 600; color: var(--ink); letter-spacing: .3px; }

  /* Back face */
  .card--back { left: 110px; top: 420px; width: 720px; height: 410px; z-index: 1; }
  .back__band { position: absolute; left: 0; right: 0; bottom: 0; height: 16px; background: var(--brand-blue); }
  .back__brand { position: absolute; left: 44px; top: 48px; display: flex; align-items: center; gap: 22px; }
  .back__mark {
    width: 84px; height: 84px; border-radius: 50%;
    border: 6px solid var(--brand-blue);
  }
  .back__name {
    font-weight: 600; font-size: 36px; letter-spacing: 2px;
    color: var(--brand-blue); text-transform: uppercase;
  }
  .back__label-row { position: absolute; left: 44px; right: 44px; top: 185px; display: flex; align-items: center; gap: 12px; }
  .back__label { font-style: italic; font-weight: 700; font-size: 19px; color: var(--brand-blue-dark); }
  .back__rule { flex: 1; height: 2px; background: linear-gradient(90deg, var(--brand-blue) 0%, var(--brand-blue) 50%, var(--rule-dark) 52%, var(--rule-dark) 100%); margin-top: 10px; }
  .contact-list { position: absolute; left: 48px; top: 245px; list-style: none; }
  .contact-list li { display: flex; align-items: center; gap: 18px; font-size: 17px; line-height: 1.55; color: var(--ink); }
  .contact-list svg, .address svg { width: 18px; height: 18px; fill: var(--brand-blue); flex: none; }
  .address { position: absolute; right: 44px; top: 268px; display: flex; align-items: center; gap: 16px; }
  .address p { text-align: right; font-size: 17px; line-height: 1.55; color: var(--ink); }
</style>
</head>
<body>

<section class="card card--front" aria-label="Business card front">
  <div class="front__ring"></div>
  <div class="front__identity">
    <p class="front__name">TalkHarbor</p>
    <p class="front__url">www.talkharbor.co.uk</p>
  </div>
</section>

<section class="card card--back" aria-label="Business card back">
  <div class="back__brand">
    <div class="back__mark"></div>
    <p class="back__name">TalkHarbor</p>
  </div>

  <div class="back__label-row">
    <span class="back__label">TalkHarbor</span>
    <span class="back__rule"></span>
  </div>

  <ul class="contact-list">
    <li>
      <svg viewBox="0 0 24 24" aria-hidden="true"><path d="M6.6 10.8a15.1 15.1 0 0 0 6.6 6.6l2.2-2.2c.3-.3.7-.4 1-.2 1.1.4 2.3.6 3.6.6.6 0 1 .4 1 1V20c0 .6-.4 1-1 1A17 17 0 0 1 3 4c0-.6.4-1 1-1h3.5c.6 0 1 .4 1 1 0 1.3.2 2.5.6 3.6.1.3 0 .7-.2 1l-2.3 2.2z"/></svg>
      <span>+44 1632 960812</span>
    </li>
    <li>
      <svg viewBox="0 0 24 24" aria-hidden="true"><path d="M2 5h20v14H2z M3.5 6.5 12 13l8.5-6.5" fill="none" stroke="#1a8fc4" stroke-width="2"/></svg>
      <span>DaniaKV@talkharbor.co.uk</span>
    </li>
    <li>
      <svg viewBox="0 0 24 24" aria-hidden="true"><circle cx="12" cy="12" r="9" fill="none" stroke="#1a8fc4" stroke-width="2"/><path d="M3 12h18M12 3c3 3 3 15 0 18M12 3c-3 3-3 15 0 18" fill="none" stroke="#1a8fc4" stroke-width="1.6"/></svg>
      <span>www.talkharbor.co.uk</span>
    </li>
  </ul>

  <div class="address">
    <p>14&nbsp; Harbour Row,<br>SE1 7QP, London, UK</p>
    <svg viewBox="0 0 24 24" aria-hidden="true"><path d="M12 2a7 7 0 0 0-7 7c0 5.2 7 13 7 13s7-7.8 7-13a7 7 0 0 0-7-7zm0 9.5A2.5 2.5 0 1 1 12 6.5a2.5 2.5 0 0 1 0 5z"/></svg>
  </div>

  <div class="back__band"></div>
</section>

</body>
</html>
```